Environmental Consultancey needs Web Design

A consultancey firm based in Papua New Guinea specialising servicing a client market primarily in Melanesia, the wider Pacific Region and South East Asia. The firm provides services to community development and resource extraction activites that incorporate sustainable livelihoods for local customary land owners with environmentally responsibile practices and a focus on maintaining biodiversity and ecosystem services. We aim to encompass Culture, Custom and Science in our approach. Our website preferentially will convey a relaxed Pacific Island feel in its colours and design rather than a sterile corporate feel. See attached logo that will need to be visible on page or which may provide basis for ideas for the page.

Target Market(s)

Our target market is primarily the oil, gas and mining industry, secondarily international donor and aid programs followed by government projects and not for profit programs. Services include:
1. Biodiversity and Conservation - Fauna and Flora survey, assessment, management, monitoring & research, protected areas & endangered & threatend species.
2. Social & Community - impact, stakeholder engagement, census and survey, land and community affairs, capacity building empowerment.
3. Environmental Management - sustainable use, enterprise development & management, biodiversity offsets.

Industry/Entity Type

Community

Requirements
Must have
• Multiple pages, Logo somewhere on home page. Space for a couple of photos that as yet ive not decieded upon.
Nice to have
• Perhaps incorporate shapes, texture and colours that convey a feel of the attached photo of a blue bird of paradise. The blue fine overlapping and interlocking feather patterns are appealing perhaps as a background and the other colours used in boarders ? Abstract is fine as would be symbolic images or tribal ambience. The company is all about blending humanity in all its forms with the environment.

```html
<!DOCTYPE html>
<html lang="en">
<head>
<meta charset="utf-8">
<title>Pasifik Environs — Home</title>
<link rel="stylesheet" href="https://fonts.googleapis.com/css2?family=Yanone+Kaffeesatz:wght@400;500&family=Cabin:wght@400&family=Open+Sans:wght@400&display=swap">
<style>
:root{
  --sky:#42c3df;
  --leaf:#1f9a4a;
  --leaf-dark:#17803c;
  --ink:#222;
  --muted:#8a8a8a;
  --field:#a4a4a4;
  --panel:#f0f0f0;
  --footer:#3b3b3b;
  --footer-head:#9c9c9c;
  --footer-text:#b4b4b4;
  --feather-a:#2c6fb8;
  --feather-b:#5fb3d9;
  --line:#333;
  --social:#2b5e9e;
}
*{box-sizing:border-box;margin:0;padding:0}
html,body{width:1139px;height:1200px;overflow:hidden;background:#fff}
body{position:relative;font-family:"Cabin",sans-serif;color:var(--ink)}
.abs{position:absolute}
.display{font-family:"Yanone Kaffeesatz",sans-serif;font-weight:400;white-space:nowrap}
.top-bar{left:0;top:0;width:1139px;height:11px;background:var(--sky)}
.nav-tab{left:467px;top:11px;width:100px;height:49px;background:var(--sky);border-radius:0 0 8px 8px}
.nav-item{top:17px;font-size:25px;color:#111;transform:translateX(-50%)}
.brand{left:60px;top:60px;display:flex;align-items:center;gap:10px;font-size:30px;color:var(--leaf)}
.brand-dot{width:26px;height:26px;border-radius:50%;background:var(--sky)}
.search-label{left:650px;top:114px;font-size:24px}
.search-box{left:719px;top:115px;width:238px;height:38px;border:1px solid var(--line);background:#fff}
.search-icon{right:6px;top:6px}
.social{top:125px;display:flex;align-items:center;gap:5px;font-size:11.5px;color:var(--social);white-space:nowrap}
.social-square{width:15px;height:15px;border-radius:3px;background:var(--sky)}
.slider{left:44px;top:239px;width:718px;height:300px;border:1px solid var(--line);background:var(--sky)}
.slide-photo{left:0;top:0;width:446px;height:298px;background:linear-gradient(135deg,#3e8f8a 0%,var(--feather-b) 35%,var(--feather-a) 65%,#1a3d66 100%)}
.slide-caption{left:0;top:258px;width:446px;height:40px;background:rgba(30,30,30,.55);color:#fff;font-size:24px;padding:4px 0 0 40px}
.slide-thumb{left:457px;width:99px;height:72px;border:2px solid #fff;background:linear-gradient(135deg,#3e8f8a,var(--feather-a))}
.slide-label{left:604px;font-size:24px;color:#111}
.slide-rule{left:456px;width:254px;height:1px;background:rgba(255,255,255,.6)}
.projects{left:780px;top:239px;width:316px;height:300px;border:1px solid var(--line);background:var(--panel)}
.projects-title{left:0;top:10px;width:100%;text-align:center;font-size:31px;color:var(--leaf)}
.projects-rule{left:18px;top:54px;width:278px;height:6px;background:radial-gradient(ellipse at center,rgba(0,0,0,.22),rgba(0,0,0,0) 70%)}
.project-thumb{width:126px;height:88px;background:linear-gradient(160deg,#9aa84a 0%,#2f6f73 45%,#1e3f5a 70%,#b9b35a 100%)}
.welcome-title{left:43px;top:568px;font-size:30px;color:#222}
.copy{left:43px;width:722px;font-size:13.8px;line-height:18px;text-align:justify;color:#222}
.btn-green{left:632px;top:958px;width:127px;height:39px;border-radius:20px;background:linear-gradient(#26a858,var(--leaf-dark));color:#fff;font-size:24px;text-align:center;line-height:39px}
.card{border:1px solid var(--line);border-radius:14px;background:#fff;overflow:hidden}
.news{left:779px;top:555px;width:317px;height:207px}
.card-title{left:0;top:6px;width:100%;text-align:center;font-size:31px}
.news-title{color:var(--sky)}
.news-item{left:14px;width:285px;font-family:"Open Sans",sans-serif;font-size:13.5px;line-height:19px;color:var(--muted);text-align:justify}
.news-date{right:20px;font-size:14px;color:var(--leaf)}
.news-more{left:0;bottom:0;width:100%;height:35px;background:#e6e6e6;display:flex;justify-content:center;align-items:center}
.enquiry{left:779px;top:772px;width:317px;height:229px}
.enquiry-title{color:var(--leaf)}
.field-label{left:17px;font-size:13.5px;color:var(--muted);white-space:nowrap}
.field{left:100px;width:203px;background:var(--field)}
.btn-grey{height:33px;border-radius:17px;background:linear-gradient(#f4f4f4,#d9d9d9);font-family:"Open Sans",sans-serif;font-size:14px;text-align:center;line-height:33px;color:#222}
.footer{left:0;top:1015px;width:1139px;height:185px;background:var(--footer)}
.footer-head{font-size:30px;color:var(--footer-head)}
.footer-text{font-family:"Open Sans",sans-serif;font-size:13.5px;line-height:19.5px;color:var(--footer-text);white-space:nowrap}
.footer-field{width:150px;height:26px;background:var(--field)}
</style>
</head>
<body>
<div class="abs top-bar"></div>

<nav>
  <div class="abs nav-tab"></div>
  <span class="abs nav-item display" style="left:514px">Home</span>
  <span class="abs nav-item display" style="left:646px">About Us</span>
  <span class="abs nav-item display" style="left:785px">Services</span>
  <span class="abs nav-item display" style="left:918px">Projects</span>
  <span class="abs nav-item display" style="left:1060px">Contact Us</span>
</nav>

<div class="abs brand display"><span class="brand-dot"></span>Pasifik Environs</div>

<div class="abs search-label display">Search :</div>
<div class="abs search-box">
  <svg class="abs search-icon" width="26" height="26" viewBox="0 0 26 26" aria-hidden="true">
    <circle cx="13" cy="13" r="12" fill="#eee"/>
    <circle cx="11" cy="11" r="5" fill="none" stroke="#444" stroke-width="2"/>
    <line x1="14.5" y1="14.5" x2="19" y2="19" stroke="#444" stroke-width="3" stroke-linecap="round"/>
  </svg>
</div>
<div class="abs social" style="left:970px"><span class="social-square"></span>Friendlink</div>
<div class="abs social" style="left:1046px"><span class="social-square"></span>Chirpline</div>

<section class="abs slider">
  <div class="abs slide-photo" role="img" aria-label="Photo of a blue bird of paradise perched on a branch"></div>
  <div class="abs slide-caption display">ENCOMPASSING CULTURE, CUSTOM &amp; SCIENCE</div>
  <div class="abs slide-thumb" style="top:14px" role="img" aria-label="Slide thumbnail photo"></div>
  <div class="abs slide-label display" style="top:36px">Slider 1</div>
  <div class="abs slide-rule" style="top:101px"></div>
  <div class="abs slide-thumb" style="top:113px" role="img" aria-label="Slide thumbnail photo"></div>
  <div class="abs slide-label display" style="top:135px">Slider 2</div>
  <div class="abs slide-rule" style="top:199px"></div>
  <div class="abs slide-thumb" style="top:212px" role="img" aria-label="Slide thumbnail photo"></div>
  <div class="abs slide-label display" style="top:234px">Slider 3</div>
</section>

<section class="abs projects">
  <h2 class="abs projects-title display">OUR PROJECTS</h2>
  <div class="abs projects-rule"></div>
  <div class="abs project-thumb" style="left:22px;top:80px" role="img" aria-label="Project photo"></div>
  <div class="abs project-thumb" style="left:171px;top:80px" role="img" aria-label="Project photo"></div>
  <div class="abs project-thumb" style="left:22px;top:188px" role="img" aria-label="Project photo"></div>
  <div class="abs project-thumb" style="left:171px;top:188px" role="img" aria-label="Project photo"></div>
</section>

<main>
  <h1 class="abs welcome-title display">Welcome to Our Website</h1>
  <p class="abs copy" style="top:624px">Sustainability is the capacity to endure. For humans, sustainability is the long-term maintenance of responsibility, which has environmental, economic, and social dimensions, and encompasses the concept of stewardship, the responsible management of resource use. In ecology, sustainability describes how biological systems remain diverse and productive over time, a necessary precondition for human well-being. Long-lived and healthy wetlands and forests are examples of sustainable biological systems.</p>
  <p class="abs copy" style="top:737px">Healthy ecosystems and environments provide vital goods and services[clarification needed]. There are two major ways of managing human impact on ecosystem services. One approach is environmental management; this approach is based largely on information gained from educated professionals in earth science, environmental science, and conservation biology. Another approach is management of consumption of resources, which is based largely on information gained from educated professionals in economics.</p>
  <p class="abs copy" style="top:837px">A sustainable environment is one where resources are conserved effectively. There are three simple rules to optimize sustainability.</p>
  <p class="abs copy" style="top:891px">Most animals and plants co evolved toward a balance that keeps an immense amount of bio diversity interacting within an environment. What makes it sustainable, is that no one organism, or system, overtakes another. What makes an environment unsustainable, is when one organism, (usually the human beings), take more resources from a location then can be reproduced, or, they add more concentration of waste.</p>
  <div class="abs btn-green display">Read More</div>
</main>

<aside class="abs card news">
  <h2 class="abs card-title news-title display">LATEST NEWS</h2>
  <p class="abs news-item" style="top:44px">A sustainable environment is one where resources are conserved effectively.</p>
  <span class="abs news-date" style="top:86px">02.03.2012</span>
  <p class="abs news-item" style="top:112px">A sustainable environment is one where resources are conserved effectively.</p>
  <span class="abs news-date" style="top:152px">02.03.2012</span>
  <div class="abs news-more">
    <svg width="32" height="14" viewBox="0 0 32 14" aria-hidden="true"><path d="M2 2 L16 11 L30 2 L30 5 L16 14 L2 5 Z" fill="#111"/></svg>
  </div>
</aside>

<aside class="abs card enquiry">
  <h2 class="abs card-title enquiry-title display">QUICK ENQUIRY</h2>
  <span class="abs field-label" style="top:62px">Name &nbsp;&nbsp;&nbsp;:</span>
  <div class="abs field" style="top:52px;height:27px"></div>
  <span class="abs field-label" style="top:98px">Email &nbsp;&nbsp;&nbsp;&nbsp;:</span>
  <div class="abs field" style="top:89px;height:27px"></div>
  <span class="abs field-label" style="top:135px">Enquiry &nbsp;:</span>
  <div class="abs field" style="top:127px;height:53px"></div>
  <div class="abs btn-grey" style="left:130px;top:188px;width:90px">Send</div>
</aside>

<footer class="abs footer">
  <h2 class="abs footer-head display" style="left:42px;top:18px">Contact Us</h2>
  <p class="abs footer-text" style="left:47px;top:64px">Address details,<br>No. Street,<br>City, Country<br>Pincode</p>
  <h2 class="abs footer-head display" style="left:425px;top:18px">Newsletter Subscription</h2>
  <span class="abs footer-text" style="left:423px;top:64px">Name &nbsp;:</span>
  <div class="abs footer-field" style="left:484px;top:61px"></div>
  <span class="abs footer-text" style="left:423px;top:101px">Email &nbsp;:</span>
  <div class="abs footer-field" style="left:484px;top:99px"></div>
  <div class="abs btn-grey" style="left:507px;top:138px;width:90px">Subscribe</div>
  <p class="abs footer-text" style="left:857px;top:76px">Copyright 2012. All Rights Reserved.</p>
</footer>
</body>
</html>
```